Fresh Dwelling Tract Guide needs a new Landing Page

I like to get a landing page or website with 2-3 pages to help target home buyers who are looking to buy homes from builders such as TW Residences, Morvik, P.L. Fennick, etc. The landing page/website to be non-cluttered and be able to explain to home buyers that there are many benefits to include me as their buyer's agent when they buy a brand new home from any builders.
I may want to incorporate a short explanation video (animated) on the landing page and then for the viewer to click on a button that will take them to another page where they can search for new homes from different builders.
Target Market(s)
Home buyers looking to buy brand new home from builders such as TW Residences, Morvik, P.L. Fennick, etc.
Industry/Entity Type
Real Estate
Number of Pages Required
2 page
Font styles to use
Requirements
Must have
- The landing page may have the explanation video at the bottom of the landing page (scrolled down) or there may be a CALL TO ACTION button that takes the viewer to the 2nd page to watch the explanation video. Once they watched the explanation video and are still interested, they can click on another CALL TO ACTION button that will take them to another website that they will be able to search for all the available new homes and register their contact information.
Should not have
- No clutters and no dark colors.

```html
<!DOCTYPE html>
<html lang="en">
<head>
<meta charset="utf-8">
<title>Fresh Dwelling Tract Guide – Landing Pages</title>
<link href="https://fonts.googleapis.com/css2?family=Open+Sans:wght@400;600;700&display=swap" rel="stylesheet">
<style>
:root{
  --sky:#d3e9ef;
  --white:#ffffff;
  --blue:#2f9fcf;
  --ink:#222222;
  --orange:#fb7d22;
  --orange-dark:#e8610f;
  --player:#2f2f2f;
  --player-grey:#6b6b6b;
  --red:#e04545;
}
*{box-sizing:border-box;margin:0;padding:0}
html,body{width:1200px;height:939px;overflow:hidden;background:var(--white)}
body{position:relative;font-family:"Open Sans",sans-serif;color:var(--ink)}
.page{position:absolute;top:0;width:600px;height:939px;background:var(--sky);overflow:hidden}
.page--landing{left:0}
.page--search{left:600px}
.abs{position:absolute}
.brand{position:absolute;left:28px;top:30px;display:flex;align-items:center;gap:8px;font-weight:700;font-size:15px;color:var(--ink);line-height:1.1}
.brand__dot{width:14px;height:14px;border-radius:50%;background:var(--orange)}
.brand small{display:block;font-weight:400;font-size:8px;letter-spacing:3px;color:var(--ink)}
.contact{position:absolute;right:28px;top:42px;text-align:right;line-height:1}
.contact__phone{font-size:11px}
.contact__cta{font-size:7px;margin-top:2px}
.lead{color:var(--blue);font-size:12px;line-height:18.7px}
.note{font-size:7.5px;line-height:9.6px;font-weight:600}
.intro{color:var(--blue);font-size:10px;line-height:19px}
.btn{position:absolute;background:var(--orange);border:2px solid var(--orange-dark);border-radius:16px}
.card{position:absolute;background:var(--white);text-align:center}
.card__text{position:absolute;left:0;right:0;font-size:7px;line-height:9.3px;font-weight:600}
.photo{position:absolute;left:0;top:0;width:100%}
.social{position:absolute;top:895px;display:flex;gap:11px}
.social span{width:18px;height:18px;border-radius:50%;background:#111;border:2px solid var(--white);box-shadow:0 0 0 1px #111}
.headline-box{position:absolute;left:626px;top:112px;width:340px;background:transparent}
.headline-box span{background:var(--white);padding:1px 8px;color:var(--blue);font-size:12px;line-height:18.7px;box-decoration-break:clone;-webkit-box-decoration-break:clone}
.price{position:absolute;left:16px;top:206px;width:100px;height:100px;border-radius:50%;background:var(--orange);padding:7px}
.price__inner{width:100%;height:100%;border-radius:50%;background:var(--white);display:flex;flex-direction:column;align-items:center;justify-content:center;border:2px solid var(--orange-dark)}
.price__title{font-size:14px;font-weight:600;line-height:1}
.price__sub{font-size:6.5px;font-weight:600;margin-top:2px}
.search{position:absolute;left:78px;top:346px;width:446px;height:30px;border-radius:15px;background:var(--white)}
.filters{position:absolute;left:496px;top:381px;font-size:7px;font-weight:600}
.results{position:absolute;left:60px;right:60px;top:412px;text-align:center;color:var(--blue);font-size:11px;line-height:19px}
</style>
</head>
<body>

<!-- Landing page -->
<section class="page page--landing">
  <svg class="abs" style="left:0;top:0" width="600" height="300" viewBox="0 0 600 300">
    <polygon points="0,0 600,0 600,240 0,288" fill="#ffffff"/>
    <defs>
      <linearGradient id="heroA" x1="0" y1="0" x2="1" y2="1">
        <stop offset="0" stop-color="#f4f4f4"/>
        <stop offset="0.5" stop-color="#d7c2ad"/>
        <stop offset="1" stop-color="#8fb3d4"/>
      </linearGradient>
    </defs>
    <polygon role="img" aria-label="Photo of a mother reading a book with her baby on a soft rug" points="368,120 440,80 600,80 600,240 430,258 380,250" fill="url(#heroA)"/>
  </svg>

  <div class="brand"><span class="brand__dot"></span><div>Maplewalk<small>HOUSE TOUR</small></div></div>
  <div class="contact"><div class="contact__phone">+00 000 000 000</div><div class="contact__cta">CALL ME NOW</div></div>

  <p class="lead abs" style="left:30px;top:113px;width:335px">Lorem ipsum dolor sit amet, consectetur adipiscing elit. Sed id aliquam ligula. Morbi eget ornare nisi. Curabitur vel quam id urna aliquet facilisis.</p>
  <p class="note abs" style="left:30px;top:183px">Lorem ipsum dolor sit amet, consectetur adipiscing elit.<br>Sed id aliquam ligula.</p>
  <div class="btn" style="left:30px;top:220px;width:162px;height:31px"></div>

  <p class="intro abs" style="left:31px;top:312px;width:340px">Lorem ipsum dolor sit amet, consectetur adipiscing elit. Sed id aliquam ligula.</p>

  <div class="card" style="left:78px;top:378px;width:127px;height:171px">
    <svg class="abs" style="left:31px;top:31px" width="60" height="56" viewBox="0 0 60 56">
      <circle cx="24" cy="24" r="20" fill="#fff" stroke="#e04545" stroke-width="4"/>
      <polygon points="14,26 24,16 34,26 31,26 31,34 17,34 17,26" fill="#555"/>
      <polygon points="40,14 48,22 48,32 40,32" fill="#888"/>
      <line x1="38" y1="38" x2="50" y2="50" stroke="#3ab5d0" stroke-width="6" stroke-linecap="round"/>
    </svg>
    <p class="card__text" style="top:113px">Lorem ipsum dolor sit<br>amet, consectetur<br>adipiscing elit.<br>Sed id aliquam ligula.</p>
  </div>
  <div class="card" style="left:238px;top:378px;width:128px;height:171px">
    <svg class="abs" style="left:37px;top:33px" width="58" height="58" viewBox="0 0 58 58">
      <rect x="2" y="2" width="12" height="48" fill="#888"/>
      <rect x="10" y="6" width="40" height="44" fill="#eee" stroke="#666" stroke-width="2"/>
      <polygon points="22,26 31,17 40,26 37,26 37,34 25,34 25,26" fill="#555"/>
      <line x1="18" y1="40" x2="38" y2="40" stroke="#666" stroke-width="2"/>
      <line x1="38" y1="48" x2="54" y2="32" stroke="#3ab5d0" stroke-width="6" stroke-linecap="round"/>
    </svg>
    <p class="card__text" style="top:113px">Lorem ipsum dolor sit<br>amet, consectetur<br>adipiscing elit.<br>Sed id aliquam ligula.</p>
  </div>
  <div class="card" style="left:399px;top:378px;width:127px;height:171px">
    <svg class="abs" style="left:36px;top:37px" width="60" height="56" viewBox="0 0 60 56">
      <circle cx="30" cy="10" r="9" fill="#e04545"/>
      <line x1="36" y1="16" x2="46" y2="26" stroke="#555" stroke-width="3"/>
      <path d="M8,36 L24,36 Q36,36 44,32 L54,28 Q56,32 50,36 L36,46 L8,46 Z" fill="#fb9a4a"/>
      <rect x="2" y="34" width="8" height="14" fill="#555"/>
    </svg>
    <p class="card__text" style="top:113px">Lorem ipsum dolor sit<br>amet, consectetur<br>adipiscing elit.<br>Sed id aliquam ligula.</p>
  </div>

  <p class="intro abs" style="left:140px;width:330px;top:578px;text-align:center">Lorem ipsum dolor sit amet, consectetur adipiscing elit. Sed id aliquam ligula.</p>

  <svg class="abs" style="left:153px;top:630px" width="302" height="197" viewBox="0 0 302 197" role="img" aria-label="Explanation video player">
    <rect width="302" height="197" fill="var(--player)"/>
    <circle cx="151" cy="89" r="36" fill="var(--player-grey)"/>
    <polygon points="141,72 141,106 170,89" fill="#fff"/>
    <rect x="5" y="168" width="292" height="3" fill="#aaa"/>
    <rect x="5" y="168" width="56" height="3" fill="var(--red)"/>
    <g fill="#fff">
      <rect x="14" y="178" width="2" height="12"/><polygon points="27,178 27,190 18,184"/>
      <polygon points="38,178 38,190 47,184"/>
      <polygon points="61,178 61,190 70,184"/><rect x="71" y="178" width="2" height="12"/>
      <circle cx="236" cy="184" r="6"/>
    </g>
    <circle cx="236" cy="184" r="2" fill="var(--player)"/>
    <rect x="258" y="179" width="15" height="10" fill="none" stroke="#fff" stroke-width="2"/>
    <path d="M283,182 v-4 h4 M293,178 h4 v4 M297,186 v4 h-4 M287,190 h-4 v-4" fill="none" stroke="#fff" stroke-width="2"/>
  </svg>

  <div class="btn" style="left:220px;top:848px;width:160px;height:31px"></div>
  <div class="social" style="left:505px"><span></span><span></span><span></span></div>
</section>

<!-- Search page -->
<section class="page page--search">
  <div class="abs" style="left:0;top:0;width:600px;height:90px;background:var(--white)"></div>
  <svg class="abs" style="left:0;top:90px" width="600" height="210" viewBox="0 0 600 210">
    <defs>
      <linearGradient id="heroB" x1="0" y1="0" x2="0" y2="1">
        <stop offset="0" stop-color="#7b86a8"/>
        <stop offset="0.45" stop-color="#d9a89a"/>
        <stop offset="0.75" stop-color="#8a8a96"/>
        <stop offset="1" stop-color="#5e5c66"/>
      </linearGradient>
    </defs>
    <polygon role="img" aria-label="Photo of a two-storey family house at sunset" points="0,0 600,0 600,208 0,186" fill="url(#heroB)"/>
    <path d="M16,46 l-6,7 l6,7 M584,46 l6,7 l-6,7" fill="none" stroke="#fff" stroke-width="2"/>
  </svg>

  <div class="brand"><span class="brand__dot"></span><div>Maplewalk<small>HOUSE TOUR</small></div></div>
  <div class="contact"><div class="contact__phone">+00 000 000 000</div><div class="contact__cta">CALL ME NOW</div></div>

  <p class="headline-box" style="left:26px"><span>Lorem ipsum dolor sit amet, consectetur adipiscing elit. Sed id aliquam ligula. Morbi eget ornare nisi. Curabitur vel quam id urna aliquet facilisis.</span></p>

  <div class="price"><div class="price__inner"><span class="price__title">Price PVP</span><span class="price__sub">0% TAX 12 Months</span></div></div>

  <div class="search">
    <svg class="abs" style="left:410px;top:4px" width="24" height="24" viewBox="0 0 24 24">
      <circle cx="9" cy="9" r="7" fill="none" stroke="#222" stroke-width="1.6"/>
      <line x1="14" y1="14" x2="21" y2="21" stroke="#222" stroke-width="2"/>
    </svg>
  </div>
  <div class="filters">Filters</div>
  <p class="results">Lorem ipsum dolor sit amet, consectetur adipiscing elit. Sed id aliquam ligula, x results find!</p>

  <div class="card" style="left:78px;top:468px;width:127px;height:171px">
    <div class="photo" style="height:84px;background:linear-gradient(135deg,#8a6b50,#e6e1d8 60%,#b9a891)" role="img" aria-label="Photo of a modern kitchen"></div>
    <p class="card__text" style="top:112px">Lorem ipsum dolor sit<br>amet, consectetur<br>adipiscing elit.<br>Sed id aliquam ligula.</p>
  </div>
  <div class="card" style="left:838px;left:238px;top:468px;width:128px;height:171px">
    <div class="photo" style="height:84px;background:linear-gradient(135deg,#f0f0f0,#9a9a9a 55%,#4a4a4a)" role="img" aria-label="Photo of a living room with a dark sofa"></div>
    <p class="card__text" style="top:112px">Lorem ipsum dolor sit<br>amet, consectetur<br>adipiscing elit.<br>Sed id aliquam ligula.</p>
  </div>
  <div class="card" style="left:399px;top:468px;width:127px;height:171px">
    <div class="photo" style="height:84px;background:linear-gradient(180deg,#c7c9cf,#7d6a5e 55%,#4d4640)" role="img" aria-label="Photo of a city street with apartment buildings"></div>
    <p class="card__text" style="top:112px">Lorem ipsum dolor sit<br>amet, consectetur<br>adipiscing elit.<br>Sed id aliquam ligula.</p>
  </div>
  <div class="card" style="left:78px;top:674px;width:127px;height:172px">
    <div class="photo" style="height:84px;background:linear-gradient(180deg,#f2eee6,#c9b9a4 60%,#8a6a4e)" role="img" aria-label="Photo of a bright living room"></div>
    <p class="card__text" style="top:116px">Lorem ipsum dolor sit<br>amet, consectetur<br>adipiscing elit.<br>Sed id aliquam ligula.</p>
  </div>
  <div class="card" style="left:238px;top:674px;width:128px;height:172px">
    <div class="photo" style="height:84px;background:linear-gradient(180deg,#5d8fd0,#8fbf6a 50%,#3f7a2e)" role="img" aria-label="Photo of a cottage in a green garden"></div>
    <p class="card__text" style="top:116px">Lorem ipsum dolor sit<br>amet, consectetur<br>adipiscing elit.<br>Sed id aliquam ligula.</p>
  </div>
  <div class="card" style="left:399px;top:674px;width:127px;height:172px">
    <div class="photo" style="height:84px;background:linear-gradient(180deg,#f4f4f4,#d8d8d8 60%,#7a6656)" role="img" aria-label="Photo of a white dining room"></div>
    <p class="card__text" style="top:116px">Lorem ipsum dolor sit<br>amet, consectetur<br>adipiscing elit.<br>Sed id aliquam ligula.</p>
  </div>

  <svg class="abs" style="left:533px;top:826px" width="20" height="20" viewBox="0 0 20 20">
    <path d="M2,3 l8,7 l8,-7 M2,10 l8,7 l8,-7" fill="none" stroke="#fff" stroke-width="2"/>
  </svg>

  <div class="social" style="left:505px"><span></span><span></span><span></span></div>
</section>

</body>
</html>
```